Recruitment Site Design

We need a design for the login page, about page, and inner pages of a recruitment site for an oil and gas company. Design should be modern, sleek, professional and colors can be blue, green, white, orange or any other recommended colors.

Please also take into consideration that once the users login, they will need to access a form to fill in their information.

** UPDATE: Kindly provide a design for the inner information page consistent with the outer design. Attached is a picture of the basic structure. ***
Updates

Please provide a design for inner pages as shown in the design brief consistent with the registration page provided. 

Reason: We're extending it to get more inside pages.

Target Market(s)

Professionals looking for a career in the oil and gas industry in the Middle East.

Industry/Entity Type

Oil And Gas

Requirements
Must have
• Sleek design

```html
<!DOCTYPE html>
<html lang="en">
<head>
<meta charset="utf-8">
<title>Recruitment Home</title>
<link rel="stylesheet" href="https://fonts.googleapis.com/css2?family=Cabin+Condensed:wght@400;500;600;700&display=swap">
<style>
:root{
  --sky:#2a9fcc;
  --sky-deep:#137fb0;
  --sky-light:#4fb6dc;
  --navy:#1d5f80;
  --navy-deep:#164c68;
  --panel:#e4e4e4;
  --card:#e9e9e9;
  --ink:#555b60;
  --ink-dark:#3d4246;
  --teal-text:#21708f;
  --link:#2a7ea3;
  --white:#ffffff;
  --footer:#1377a6;
  --footer-deep:#0e5f88;
}
*{box-sizing:border-box;margin:0;padding:0}
html,body{width:1200px;height:1142px;overflow:hidden}
body{position:relative;background:var(--white);font-family:"Cabin Condensed",sans-serif;color:var(--ink)}
.abs{position:absolute}

.masthead{left:0;top:0;width:1200px;height:170px;background:linear-gradient(#2aa4d0,#1a8cbd)}
.brand{left:114px;top:52px;font-size:60px;font-weight:500;color:var(--white);line-height:1;letter-spacing:-0.5px}
.social{top:56px;width:40px;height:58px}
.social-kiv{left:933px}
.social-oru{left:1005px}
.social span{position:absolute;left:0;top:15px;width:40px;text-align:center;font-size:12px;font-weight:600;color:var(--white)}

.main-nav{left:108px;top:142px;width:983px;height:51px;border-radius:5px;background:linear-gradient(#5cbde2,#2c9fd0 60%,#2590c0);box-shadow:0 2px 3px rgba(0,0,0,.25)}
.main-nav .item{position:absolute;top:0;height:48px;line-height:50px;font-size:14px;font-weight:600;color:#16506d;text-align:center;letter-spacing:.3px}
.main-nav .item.active{color:var(--white);background:linear-gradient(#4bb3dc,#2b9ccb);border-bottom:3px solid #1878a5;border-radius:5px 0 0 0}
.main-nav .divider{position:absolute;top:0;width:1px;height:51px;background:rgba(255,255,255,.35)}
.search{left:709px;top:13px;width:258px;height:26px;border-radius:4px;background:linear-gradient(#1a86b8,#2797c7);border:1px solid #62c0e4}
.search span{position:absolute;left:8px;top:4px;font-size:14px;color:#d9f0fa}
.search-btn{position:absolute;right:2px;top:2px;width:22px;height:20px;border-radius:3px;background:#3cb8e6}

.slider{left:108px;top:212px;width:980px;height:408px;border-radius:14px;background:var(--panel)}
.slide{left:19px;top:19px;width:942px;height:339px;border-radius:20px;background:linear-gradient(#d5e6ef 0%,#a9c9dc 25%,#3f7eaa 45%,#24608f 100%);box-shadow:inset 0 0 0 2px rgba(0,0,0,.08)}
.arrow{top:157px;width:40px;height:56px;background:#eef2f4;display:flex;align-items:center;justify-content:center}
.arrow-prev{left:19px;border-radius:0 8px 8px 0}
.arrow-next{left:920px;border-radius:8px 0 0 8px}
.dots{left:0;top:376px;width:980px;display:flex;justify-content:center;gap:6px}
.dot{width:12px;height:12px;border-radius:50%;background:#5c5c5c}
.dot.on{background:#27a6dc}
.slider-shadow{left:40px;top:625px;width:1120px;height:16px;border-radius:50%;background:radial-gradient(ellipse at center,rgba(0,0,0,.18),rgba(0,0,0,0) 70%)}

.welcome{left:110px;top:670px;width:638px;height:314px;background:var(--card);border:1px solid #cfcfcf;box-shadow:inset 0 0 0 1px #fff}
.welcome h1{position:absolute;left:23px;top:20px;font-size:22px;font-weight:400;color:var(--teal-text)}
.welcome .rule{position:absolute;left:22px;top:51px;width:599px;height:1px;background:#a9a9a9}
.team-photo{left:22px;top:66px;width:109px;height:93px;border:2px solid #c6d2d9;background:linear-gradient(#f6f6f6,#d9d9d9 60%,#a8a8a8)}
.intro{left:142px;top:68px;width:474px;font-size:14px;line-height:22px;text-align:justify;color:var(--ink);letter-spacing:.2px}
.features-title{left:23px;top:179px;font-size:15px;font-weight:500;color:var(--ink-dark)}
.features{left:36px;top:201px;list-style:none}
.features li{height:22px;font-size:14px;color:var(--link);padding-left:18px;position:relative;line-height:22px}
.features li::before{content:"";position:absolute;left:0;top:8px;border-left:9px solid var(--navy);border-top:4px solid transparent;border-bottom:4px solid transparent}
.more-btn{left:22px;top:272px;width:63px;height:31px;border-radius:3px;background:linear-gradient(#3eb0df,#1981b3);border:1px solid #16739f;color:var(--white);font-size:15px;font-weight:600;text-align:center;line-height:29px}

.login{left:771px;top:670px;width:308px;height:314px;background:linear-gradient(#1f6c90,#1b5c7d);border:1px solid #10435d;box-shadow:inset 0 0 0 1px rgba(255,255,255,.15)}
.login .handle{position:absolute;left:102px;top:22px;width:104px;height:14px;border-radius:7px;background:#1e2e36;border:2px solid #8c9aa2}
.login h2{position:absolute;left:0;top:52px;width:306px;text-align:center;font-size:18px;font-weight:600;color:var(--white);letter-spacing:.4px}
.field{left:28px;width:251px;height:35px;border-radius:4px;background:var(--white);border:2px solid #10435d}
.field-user{top:88px}
.field-pass{top:141px}
.field svg{position:absolute;left:10px;top:8px}
.field span{position:absolute;left:36px;top:7px;font-size:14px;color:#3f454a}
.login-btn{left:29px;top:194px;width:249px;height:54px;border-radius:4px;background:#164c68;border:1px solid #3d88ab;padding:4px}
.login-btn div{width:100%;height:100%;border-radius:3px;background:linear-gradient(#44aedb 0%,#2d9ccd 48%,#1383b8 50%,#1d8fc3 100%);text-align:center;line-height:44px;font-size:17px;font-weight:600;color:#123f57;letter-spacing:.5px}
.remember{left:30px;top:263px;font-size:13px;color:var(--white);display:flex;align-items:center;gap:6px}
.checkbox{width:17px;height:17px;border-radius:3px;background:#d4d8da;border:1px solid #0f3f57;display:flex;align-items:center;justify-content:center}
.forgot{left:178px;top:264px;font-size:13px;color:var(--white)}
.card-shadow{top:988px;height:20px;border-radius:50%;background:radial-gradient(ellipse at center,rgba(0,0,0,.16),rgba(0,0,0,0) 70%)}

.footer{left:0;top:1044px;width:1200px;height:98px;background:linear-gradient(var(--footer),var(--footer-deep))}
.footer-nav{left:0;top:32px;width:1200px;text-align:center;font-size:14px;color:#0d2f44;letter-spacing:.3px}
.footer-nav .sep{margin:0 13px}
.footer-nav .current{color:var(--white)}
.copyright{left:0;top:55px;width:1200px;text-align:center;font-size:13px;color:#0d2f44;letter-spacing:.3px}
</style>
</head>
<body>

<header class="masthead abs">
  <div class="brand abs">Company Logo</div>
  <a class="social social-kiv abs" aria-label="Kiv">
    <svg width="40" height="58" viewBox="0 0 40 58"><path d="M2 0H38V44L20 56L2 44Z" fill="#2a9bc9" stroke="#1a6f97" stroke-width="2"/></svg>
    <span>Kiv</span>
  </a>
  <a class="social social-oru abs" aria-label="Oru">
    <svg width="40" height="58" viewBox="0 0 40 58"><path d="M2 0H38V44L20 56L2 44Z" fill="#2a9bc9" stroke="#1a6f97" stroke-width="2"/></svg>
    <span>Oru</span>
  </a>
</header>

<nav class="main-nav abs">
  <a class="item active" style="left:0;width:125px">HOME</a>
  <span class="divider" style="left:125px"></span>
  <a class="item" style="left:126px;width:121px">ABOUT US</a>
  <span class="divider" style="left:247px"></span>
  <a class="item" style="left:248px;width:131px">FIND JOB</a>
  <span class="divider" style="left:379px"></span>
  <a class="item" style="left:380px;width:165px">REGISTER HERE</a>
  <span class="divider" style="left:545px"></span>
  <a class="item" style="left:546px;width:128px">CONTACT US</a>
  <div class="search abs">
    <span>Search here...</span>
    <div class="search-btn">
      <svg width="22" height="20" viewBox="0 0 22 20"><circle cx="10" cy="9" r="5" fill="none" stroke="#0f4d6d" stroke-width="2"/><path d="M14 13L17 16" stroke="#0f4d6d" stroke-width="2.5" stroke-linecap="round"/></svg>
    </div>
  </div>
</nav>

<section class="slider abs">
  <div class="slide abs" role="img" aria-label="Offshore oil rig at sea with an engineer in a hard hat holding a clipboard"></div>
  <a class="arrow arrow-prev abs" aria-label="Previous slide">
    <svg width="20" height="30" viewBox="0 0 20 30"><path d="M16 3L4 15L16 27" fill="none" stroke="#3d7fa5" stroke-width="3"/></svg>
  </a>
  <a class="arrow arrow-next abs" aria-label="Next slide">
    <svg width="20" height="30" viewBox="0 0 20 30"><path d="M4 3L16 15L4 27" fill="none" stroke="#3d7fa5" stroke-width="3"/></svg>
  </a>
  <div class="dots abs"><span class="dot on"></span><span class="dot"></span><span class="dot"></span></div>
</section>
<div class="slider-shadow abs"></div>

<section class="welcome abs">
  <h1>Welcome to our site</h1>
  <div class="rule"></div>
  <div class="team-photo abs" role="img" aria-label="Group of professional team members"></div>
  <p class="intro abs">We need a design for the login page, about page, and inner pages of a recruitment site for an oil and gas company. Design should be modern, sleek, professional and colors can be blue, green, white, orange or any other recommended colors. We need a design for the login page, about page, and inner pages of a recruitment site for an oil and gas company.</p>
  <p class="features-title abs">Our Feature envioronment for employee to encourage them to join us :</p>
  <ul class="features abs">
    <li>Write here something about your esteemed company that encourage the job seekers.</li>
    <li>Write here something about your esteemed company that encourage the job seekers.</li>
    <li>Write here something about your esteemed company that encourage the job seekers.</li>
  </ul>
  <a class="more-btn abs">More</a>
</section>
<div class="card-shadow abs" style="left:130px;width:600px"></div>

<section class="login abs">
  <div class="handle"></div>
  <h2>MEMBER LOGIN</h2>
  <div class="field field-user abs">
    <svg width="16" height="16" viewBox="0 0 16 16"><circle cx="8" cy="5" r="3.5" fill="#b5b9bc"/><path d="M1 16C1 11 4 9.5 8 9.5S15 11 15 16Z" fill="#b5b9bc"/></svg>
    <span>Username</span>
  </div>
  <div class="field field-pass abs">
    <svg width="16" height="16" viewBox="0 0 16 16"><path d="M5 7V5a3 3 0 0 1 6 0v2" fill="none" stroke="#b5b9bc" stroke-width="2"/><rect x="3" y="7" width="10" height="8" rx="1" fill="#b5b9bc"/></svg>
    <span>Password</span>
  </div>
  <a class="login-btn abs"><div>LOGIN</div></a>
  <label class="remember abs">
    <span class="checkbox"><svg width="11" height="10" viewBox="0 0 11 10"><path d="M1 5L4 8L10 1" fill="none" stroke="#1d4c63" stroke-width="2.2"/></svg></span>
    Remember Me
  </label>
  <a class="forgot abs">Forgot Password?</a>
</section>
<div class="card-shadow abs" style="left:790px;width:270px"></div>

<footer class="footer abs">
  <p class="footer-nav abs"><span class="current">HOME</span><span class="sep">|</span>ABOUT US<span class="sep">|</span>FIND JOB<span class="sep">|</span>REGISTER HERE<span class="sep">|</span>CONTACT US</p>
  <p class="copyright abs">COPYRIGHT @ 2012, COMPANY NAME</p>
</footer>

</body>
</html>
```